Lifecoach needs website design based on a standard Wordpress theme

I need a website for my new lifecoaching business that can be easily implemented in Wordpress, it needs to be compatible with a standard Wordpress theme. So I can place the pictures, texts etc. in a standard theme of Wordpress.

I want the design to be a very good feeling and playfull one, based on my logo.

Target Market(s)

I will coach people to reach their goals and dreams in life.

Industry/Entity Type

Business

Requirements
Must have
• Can be easy implemented in Wordpress.
Nice to have
• Photo's of nature are nice.

```html
<!DOCTYPE html>
<html lang="en">
<head>
<meta charset="utf-8">
<title>Mara Lindqvist Lifecoach</title>
<link href="https://fonts.googleapis.com/css2?family=Titillium+Web:wght@400;600;700&family=Open+Sans:wght@400;600&display=swap" rel="stylesheet">
<style>
:root{
  --blue:#1a8fd6;
  --blue-dark:#0a6fb0;
  --blue-nav:#1195d8;
  --blue-nav-dark:#0579b8;
  --blue-active:#23b2e3;
  --ink:#1e1e1e;
  --text:#555;
  --muted:#888;
  --band:#e6e7e8;
  --page:#f6f6f6;
  --footer-top:#4a4a4a;
  --footer-bottom:#222;
  --white:#fff;
  --green:#3aa335;
}
*{margin:0;padding:0;box-sizing:border-box}
html,body{width:690px;height:1200px;overflow:hidden;background:var(--page)}
body{font-family:"Open Sans",Arial,sans-serif;color:var(--text)}
.page{position:relative;width:690px;height:1200px;overflow:hidden;background:var(--page)}
.abs{position:absolute}

/* header */
.site-header{left:0;top:0;width:690px;height:60px;background:linear-gradient(#fdfdfd,#ececec)}
.brand{left:100px;top:16px;display:flex;align-items:center;gap:6px}
.brand-dot{width:30px;height:30px;border-radius:50%;border:2px solid var(--blue)}
.brand-name{font-family:"Open Sans",Arial,sans-serif;font-weight:600;font-size:11.5px;line-height:13px;color:var(--blue-dark)}
.search{left:428px;top:28px;width:90px;height:16px;background:#6fa6d6;color:#e8f1fb;font-size:6.5px;font-style:italic;padding:4px 5px}
.search svg{position:absolute;right:4px;top:3px}
.social-top{left:524px;top:28px;display:flex;gap:3px}
.social-top span{width:15px;height:15px;border-radius:50%;background:#222}

/* nav */
.main-nav{left:0;top:60px;width:690px;height:33px;background:linear-gradient(var(--blue-nav),var(--blue-nav-dark))}
.main-nav ul{list-style:none;display:flex;position:absolute;left:98px;top:0;height:33px}
.main-nav li{height:33px;padding:0 10px;font-size:9.5px;letter-spacing:1px;color:var(--white);line-height:33px;border-right:1px solid rgba(0,0,0,.2)}
.main-nav li:last-child{border-right:0}
.main-nav li.active{background:var(--blue-active)}

/* hero */
.hero{left:0;top:93px;width:690px;height:305px;background:linear-gradient(#6e9bcf 0%,#c5d8ea 45%,#e8eef2 62%,#7fae45 68%,#4f8a23 100%)}
.hero-caption{left:98px;top:108px;width:318px;height:66px;background:rgba(80,85,90,.72);color:var(--white);font-size:14.5px;line-height:22px;padding:10px 14px}
.hero-arrow{top:125px}

/* services */
.section-title{font-family:"Titillium Web",Arial,sans-serif;font-weight:700;color:var(--ink);text-align:center;letter-spacing:1.5px;width:690px;left:0}
.services-title{top:413px;font-size:21px}
.services-sub{top:444px;width:690px;left:0;text-align:center;font-size:8.5px;color:#444;font-family:"Titillium Web",Arial,sans-serif}
.service{top:472px;width:160px;text-align:center}
.service-icon{width:80px;height:80px;border-radius:50%;background:var(--blue-nav);margin:0 auto;display:flex;align-items:center;justify-content:center}
.service h3{font-family:"Titillium Web",Arial,sans-serif;font-weight:700;font-size:11.5px;line-height:15px;color:var(--ink);margin-top:16px}
.service p{font-family:"Titillium Web",Arial,sans-serif;font-size:7.8px;line-height:11px;color:var(--muted);margin-top:6px}

/* guide */
.guide{left:0;top:646px;width:690px;height:180px;background:linear-gradient(90deg,#e4e5e6,#eeeeef 60%,#dcdddf)}
.guide h2{left:99px;top:18px;font-family:"Titillium Web",Arial,sans-serif;font-weight:400;font-size:14px;letter-spacing:1.4px;color:var(--blue-dark)}
.guide p{left:99px;top:43px;width:248px;font-family:Arial,sans-serif;font-size:7.4px;line-height:12.3px;letter-spacing:.4px;color:#666;text-align:justify}
.read-more{left:99px;top:140px;width:74px;height:19px}
.devices{left:365px;top:4px;width:230px;height:170px;background:radial-gradient(ellipse at center,#fdfdfd 0%,#d9dadc 70%,transparent 72%);border-radius:8px}

/* courses */
.courses-title{top:838px;font-size:19.5px}
.course{top:885px;width:109px;height:109px}
.course-1{left:112px;background:linear-gradient(#7c9a7a,#5d7a5a)}
.course-2{left:230px;background:linear-gradient(#b26a5c,#4a3a38)}
.course-3{left:349px;background:linear-gradient(#e8b9a0,#e05a5a)}
.course-4{left:467px;background:linear-gradient(#b9bcbf,#6d7175)}
.course-overlay{position:absolute;left:10px;top:21px;color:var(--white)}
.course-overlay h4{font-family:"Titillium Web",Arial,sans-serif;font-weight:700;font-size:10px;line-height:11px}
.course-overlay p{font-size:6.5px;margin-top:4px}
.course-overlay .share{display:flex;gap:9px;margin-top:10px}
.course-overlay .share span{width:16px;height:16px;border-radius:50%;border:1px solid rgba(255,255,255,.8)}

/* testimonial */
.avatar{left:123px;top:1035px;width:56px;height:56px;border-radius:50%;border:3px solid var(--white);background:linear-gradient(#e9c99c,#c98a66);box-shadow:0 1px 3px rgba(0,0,0,.2)}
.quote-mark{font-family:Georgia,serif;font-size:34px;font-weight:700;color:#0f5f8a;line-height:1}
.quote-open{left:202px;top:1030px}
.quote-close{left:535px;top:1062px}
.quote-text{left:228px;top:1041px;width:310px;font-size:8px;line-height:12px;color:#444}
.quote-author{display:block;color:var(--green);font-style:italic;margin-top:1px}

/* footer */
.site-footer{left:0;top:1109px;width:690px;height:91px;background:linear-gradient(var(--footer-top),var(--footer-bottom))}
.footer-links{left:0;top:18px;width:690px;text-align:center;font-family:Arial,sans-serif;font-size:6.6px;color:var(--white)}
.copyright{left:99px;top:56px;font-family:Arial,sans-serif;font-size:6px;color:var(--white)}
.social-footer{left:275px;top:47px;display:flex;gap:5px}
.social-footer span{width:19px;height:19px;border-radius:50%;background:#f2f2f2}
.newsletter{left:469px;top:50px;width:119px;height:15px;background:var(--white);font-size:5.5px;color:#555;padding:4px 5px}
.newsletter svg{position:absolute;right:4px;top:2px}
</style>
</head>
<body>
<div class="page">

  <header class="site-header abs">
    <div class="brand abs">
      <span class="brand-dot"></span>
      <span class="brand-name">Mara Lindqvist<br>Lifecoach</span>
    </div>
    <div class="search abs">Search...
      <svg width="9" height="9" viewBox="0 0 10 10"><circle cx="4" cy="4" r="3" fill="none" stroke="#fff" stroke-width="1.4"/><line x1="6.2" y1="6.2" x2="9" y2="9" stroke="#fff" stroke-width="1.6"/></svg>
    </div>
    <div class="social-top abs"><span></span><span></span><span></span><span></span></div>
  </header>

  <nav class="main-nav abs">
    <ul>
      <li class="active">HOME</li>
      <li>ABOUT US</li>
      <li>LIFE COACHING »</li>
      <li>SUCCESS STORIES</li>
      <li>CONTACTS</li>
    </ul>
  </nav>

  <section class="hero abs" role="img" aria-label="Joyful woman jumping against a blue sky above a green meadow">
    <div class="hero-caption abs">We specialize in transition life coaching for personal and professional empowerment</div>
    <svg class="hero-arrow abs" style="left:55px" width="20" height="55" viewBox="0 0 20 55"><polyline points="18,2 2,27.5 18,53" fill="none" stroke="#fff" stroke-width="2"/></svg>
    <svg class="hero-arrow abs" style="left:615px" width="20" height="55" viewBox="0 0 20 55"><polyline points="2,2 18,27.5 2,53" fill="none" stroke="#fff" stroke-width="2"/></svg>
  </section>

  <h2 class="section-title services-title abs">SERVICES WE PROVIDE</h2>
  <p class="services-sub abs">Duis mollis, est non commodo luctus, nisi erat porttitor ligula, eget lacinia odio sem nec elit.</p>

  <div class="service abs" style="left:100px">
    <div class="service-icon">
      <svg width="40" height="34" viewBox="0 0 40 34"><ellipse cx="15" cy="14" rx="14" ry="10" fill="#fff"/><polygon points="6,20 4,30 14,22" fill="#fff"/><ellipse cx="25" cy="12" rx="12" ry="9" fill="none" stroke="#fff" stroke-width="2"/></svg>
    </div>
    <h3>HOW WE CAN<br>HELP YOU?</h3>
    <p>Lorem ipsum dolor sit amet,<br>consectetuer adipiscing elit,</p>
  </div>
  <div class="service abs" style="left:260px">
    <div class="service-icon">
      <svg width="38" height="34" viewBox="0 0 38 34"><rect x="2" y="2" width="34" height="22" fill="none" stroke="#fff" stroke-width="3"/><rect x="16" y="24" width="6" height="5" fill="#fff"/><rect x="10" y="29" width="18" height="3" fill="#fff"/></svg>
    </div>
    <h3>WHAT IS ONLINE<br>COACHING?</h3>
    <p>Sed ut perspiciatis unde<br>omnis iste natus error sit</p>
  </div>
  <div class="service abs" style="left:420px">
    <div class="service-icon">
      <svg width="50" height="32" viewBox="0 0 50 32"><circle cx="12" cy="11" r="6" fill="#fff"/><circle cx="38" cy="11" r="6" fill="#fff"/><path d="M1 30 Q12 14 23 30Z" fill="#fff"/><path d="M27 30 Q38 14 49 30Z" fill="#fff"/><circle cx="25" cy="8" r="7" fill="#fff" stroke="var(--blue-nav)" stroke-width="1.5"/><path d="M12 32 Q25 12 38 32Z" fill="#fff" stroke="var(--blue-nav)" stroke-width="1.5"/></svg>
    </div>
    <h3>BEST COACHES<br>ARE HERE</h3>
    <p>At vero eos et accusamus et<br>iusto odio dignissimos qui</p>
  </div>

  <section class="guide abs">
    <h2 class="abs">GUIDE TO LIFE COACHING</h2>
    <p class="abs">Praesent vestibulum molestie lacus. Aenean nonummy hendrerit mauris. Phasellus porta. Fusce suscipit varius mi. Cum sociis natoque penatibus et magnis dis parturient montes, nascetur ridiculus mus. Nulla dui. Fusce feugiat malesuada odio. Morbi nunc odio, gravida at, cursus nec, luctus a, lorem. Maecenas tristique orci ac sem. Duis ultricies pharetra magna. Donec accumsan malesuada orci. Donec sit amet eros.</p>
    <svg class="read-more abs" viewBox="0 0 74 19" aria-label="Read more">
      <defs><linearGradient id="btn" x1="0" y1="0" x2="0" y2="1"><stop offset="0" stop-color="#3aa6e4"/><stop offset="1" stop-color="#1174b5"/></linearGradient></defs>
      <path d="M3 0H64L74 9.5L64 19H3Q0 19 0 16V3Q0 0 3 0Z" fill="url(#btn)"/>
      <text x="10" y="12.8" font-family="Titillium Web, sans-serif" font-weight="700" font-size="8" fill="#fff">READ MORE</text>
    </svg>
    <div class="devices abs" role="img" aria-label="Desktop monitor, tablet and phone showing the website"></div>
  </section>

  <h2 class="section-title courses-title abs">OUR COURSES</h2>
  <svg class="abs" style="left:55px;top:913px" width="18" height="52" viewBox="0 0 18 52"><polyline points="16,1 2,26 16,51" fill="none" stroke="#555" stroke-width="1"/></svg>
  <svg class="abs" style="left:616px;top:913px" width="18" height="52" viewBox="0 0 18 52"><polyline points="2,1 16,26 2,51" fill="none" stroke="#555" stroke-width="1"/></svg>

  <div class="course course-1 abs" role="img" aria-label="Couple embracing outdoors">
    <div class="course-overlay">
      <h4>LOVE &amp;<br>RELATIONSHIPS</h4>
      <p>Praesent vestibulum molesti</p>
      <div class="share"><span></span><span></span></div>
    </div>
  </div>
  <div class="course course-2 abs" role="img" aria-label="Smiling woman holding banknotes"></div>
  <div class="course course-3 abs" role="img" aria-label="Woman jogging in a red top"></div>
  <div class="course course-4 abs" role="img" aria-label="Thoughtful woman beneath light bulb bubbles"></div>

  <div class="avatar abs" role="img" aria-label="Portrait of client Jane Doe"></div>
  <span class="quote-mark quote-open abs">“</span>
  <p class="quote-text abs">Vis id minim dicant sensibus. Pri aliquip conclusionemque ad, ad malis evertitur torquatos his. Has ei solum harum reprimique, id illum saperet tractatos his. Ei omnis soleat antiopam quo. Ad augue inani postulant mel, mel ea qualisque forensibus.<span class="quote-author">Jane Doe</span></p>
  <span class="quote-mark quote-close abs">”</span>

  <footer class="site-footer abs">
    <p class="footer-links abs">Terms of Service | Returns | Policy Privacy | Event | Contact | Blog | Sitemap</p>
    <p class="copyright abs">Copy Right © 2014. All rights reserved.</p>
    <div class="social-footer abs"><span></span><span></span><span></span><span></span><span></span><span></span></div>
    <div class="newsletter abs">News Letter
      <svg width="17" height="11" viewBox="0 0 17 11"><rect x="1" y="1" width="15" height="9" fill="none" stroke="#222" stroke-width="1.4"/><polyline points="1,1 8.5,6.5 16,1" fill="none" stroke="#222" stroke-width="1.4"/></svg>
    </div>
  </footer>

</div>
</body>
</html>
```